Brightfield Ventures Inc. Letterhead

Creation of attractive and eye catching letterhead for a business start-up for the construction industry. Letterhead must relate to construction, but avoid standard hammer and tools in the design.

I forgot to add some details, sorry about that. Some pertinent info: Ph: 916-555-0187 brightfieldventures.example 448 Willowmere Ave, Ste 210 Folsom, CA 95999 info@brightfieldventures.example not sure if slogan should be in there" “Connecting construction professionals to create a purpose driven industry.” must be able to be used in word. Thanks!

```html
<!DOCTYPE html>
<html lang="en">
<head>
<meta charset="utf-8">
<title>Brightfield Ventures Inc. Letterhead</title>
<link href="https://fonts.googleapis.com/css2?family=Open+Sans:wght@400;600;700&family=Montserrat:wght@600&display=swap" rel="stylesheet">
<style>
  :root {
    --backdrop: #e9e9ea;
    --paper: #ffffff;
    --ink: #3a3a3a;
    --ink-strong: #2b2b2b;
    --brand-red: #c10d0d;
    --brand-navy: #1c2a5e;
    --footer-text: #ffffff;
    --signature-tone: #d9d9d9;
  }
  * { margin: 0; padding: 0; box-sizing: border-box; }
  html, body {
    width: 1200px; height: 784px; overflow: hidden;
    background: var(--backdrop);
  }
  .canvas {
    width: 1200px; height: 784px;
    display: flex; align-items: center; justify-content: center;
  }
  .letterhead {
    position: relative;
    width: 524px; height: 740px;
    background: var(--paper);
    box-shadow: 0 6px 24px rgba(0,0,0,0.12);
    font-family: "Open Sans", Arial, sans-serif;
    color: var(--ink);
    overflow: hidden;
  }
  .brand {
    position: absolute; top: 44px; left: 46px;
    display: flex; align-items: center; gap: 8px;
  }
  .brand-mark {
    width: 14px; height: 14px; background: var(--brand-red);
  }
  .brand-name {
    font-family: "Montserrat", Arial, sans-serif;
    font-weight: 600; font-size: 13px; letter-spacing: 1.5px;
    color: var(--brand-navy); text-transform: uppercase;
  }
  .brand-rule {
    position: absolute; top: 68px; left: 46px;
    width: 150px; height: 1.5px; background: var(--brand-red);
  }
  .letter-body {
    position: absolute; top: 118px; left: 46px; right: 80px;
    font-size: 9.5px; line-height: 1.45;
  }
  .salutation {
    font-weight: 700; font-size: 11.5px; color: var(--ink-strong);
    margin-bottom: 8px;
  }
  .letter-body p { margin-bottom: 13px; }
  .signature {
    position: absolute; top: 480px; left: 46px;
    width: 120px; height: 48px;
    background: linear-gradient(90deg, var(--signature-tone), #f3f3f3);
    border-radius: 3px;
  }
  .footer {
    position: absolute; left: 0; bottom: 0; width: 524px; height: 84px;
  }
  .footer-band { position: absolute; inset: 0; width: 100%; height: 100%; }
  .footer-contacts {
    position: absolute; left: 16px; right: 16px; bottom: 16px;
    display: flex; justify-content: space-between; align-items: center;
    font-size: 7.2px; line-height: 1; color: var(--footer-text);
    white-space: nowrap;
  }
  .contact { display: inline-flex; align-items: center; gap: 3px; }
  .contact-icon {
    flex: 0 0 8px; width: 8px; height: 8px;
    fill: var(--footer-text);
  }
</style>
</head>
<body>
<main class="canvas">
  <article class="letterhead">
    <header>
      <div class="brand">
        <span class="brand-mark"></span>
        <span class="brand-name">Brightfield Ventures Inc.</span>
      </div>
      <div class="brand-rule"></div>
    </header>

    <section class="letter-body">
      <p class="salutation">Dear Mr. John,</p>
      <p>Lorem Ipsum is simply dummy text of the printing and typesetting industry. Lorem Ipsum has been the industry's standard dummy text ever since the 1500s, when an unknown printer took a galley of type and scrambled it to make a type specimen book. It has survived not only five centuries, but also the leap into electronic typesetting, remaining essentially unchanged.</p>
      <p>The standard chunk of Lorem Ipsum used since the 1500s is reproduced below for those interested. Sections 1.10.32 and 1.10.33 from "de Finibus Bonorum et Malorum" by Cicero are also reproduced in their exact original form, accompanied by English versions from the 1914 translation by H. Rackham.</p>
      <p>Lorem Ipsum is simply dummy text of the printing and typesetting industry. Lorem Ipsum has been the industry's standard dummy text ever since the 1500s, when an unknown printer took a galley of type and scrambled it to make a type specimen book. It has survived not only five centuries, but also the leap into electronic typesetting, remaining essentially unchanged. It was popularised in the</p>
      <p>The standard chunk of Lorem Ipsum used since the 1500s is reproduced below for those interested. Sections 1.10.32 and 1.10.33 from "de Finibus Bonorum et Malorum" by Cicero are also reproduced in their exact original form, accompanied by English versions from the 1914 translation by H. Rackham.</p>
    </section>

    <div class="signature" role="img" aria-label="Handwritten signature"></div>

    <footer class="footer">
      <svg class="footer-band" viewBox="0 0 524 84" preserveAspectRatio="none" aria-hidden="true">
        <path d="M200 42 C330 40 430 24 524 4 L524 10 C430 30 330 46 200 48 Z" fill="var(--brand-navy)"/>
        <path d="M0 48 L200 48 C330 46 430 30 524 10 L524 84 L0 84 Z" fill="var(--brand-red)"/>
      </svg>
      <div class="footer-contacts">
        <span class="contact">
          <svg class="contact-icon" viewBox="0 0 24 24" aria-hidden="true"><path d="M6.6 10.8a15 15 0 0 0 6.6 6.6l2.2-2.2c.3-.3.7-.4 1-.2 1.1.4 2.3.6 3.6.6.6 0 1 .4 1 1V20c0 .6-.4 1-1 1A17 17 0 0 1 3 4c0-.6.4-1 1-1h3.5c.6 0 1 .4 1 1 0 1.3.2 2.5.6 3.6.1.3 0 .7-.2 1z"/></svg>
          <span>916-555-0187</span>
        </span>
        <span class="contact">
          <svg class="contact-icon" viewBox="0 0 24 24" aria-hidden="true"><path d="M2 5h20v14H2z"/></svg>
          <span>info@brightfieldventures.example</span>
        </span>
        <span class="contact">
          <svg class="contact-icon" viewBox="0 0 24 24" aria-hidden="true"><circle cx="12" cy="12" r="10"/></svg>
          <span>www.brightfieldventures.example</span>
        </span>
        <span class="contact">
          <svg class="contact-icon" viewBox="0 0 24 24" aria-hidden="true"><path d="M12 2a7 7 0 0 0-7 7c0 5 7 13 7 13s7-8 7-13a7 7 0 0 0-7-7z"/></svg>
          <span>448 Willowmere Ave, Ste 210, Folsom, CA 95999</span>
        </span>
      </div>
    </footer>
  </article>
</main>
</body>
</html>
```